New Innovative Counselling and psychotherapy Service needs Business Card design

Keep it simple and professional. On one side, just company name and logo (perhaps in all blue) and maybe a tag line.

On other side (all white) my name and Qualifications in centre

Industry/Entity Type

Health And Wellness

Contact Information for Business Card

Dara Whelby
Counsellor & Psychotherapist
MA (Clin. Psych.), BSc, Dip. (Family & Syst.), PG.Dip (DBT), FGTrK, ONRE

I will also require Mobile no, Email and web site address of which I'll pass on to final designer.

Font styles to use
Sans Serif

Requirements
Must have
• My Logo Only and please use the colours in logo that is in it.
Should not have
• Any other images

```html
<!DOCTYPE html>
<html lang="en">
<head>
<meta charset="utf-8">
<title>Brightwell Lane – Business Card</title>
<link rel="stylesheet" href="https://fonts.googleapis.com/css2?family=Source+Sans+3:ital,wght@0,400;0,600;1,400&family=Raleway:wght@400&display=swap">
<style>
  :root {
    --backdrop: #808080;
    --card-blush: #fdf3f4;
    --brand-blue: #45b3ec;
    --brand-green: #9bd45d;
    --card-white: #ffffff;
    --ink-dark: #333333;
    --ink-tagline: #4a4a4a;
    --ghost-grey: #d9d9d9;
  }
  * { margin: 0; padding: 0; box-sizing: border-box; }
  html, body {
    width: 1200px; height: 802px; overflow: hidden;
    background: var(--backdrop);
  }
  .canvas { position: relative; width: 1200px; height: 802px; }

  .card {
    position: absolute; top: 274px;
    width: 443px; height: 265px; overflow: hidden;
  }

  /* Contact side */
  .card--contact { left: 136px; background: var(--card-blush); }
  .contact-panel {
    position: absolute; left: 118px; top: 0; right: 0; bottom: 0;
    background: var(--brand-blue);
    border-bottom-left-radius: 10px;
  }
  .symbol-area {
    position: absolute; left: 8px; top: 0; width: 235px; height: 265px;
    border-radius: 118px 118px 0 0;
    background: linear-gradient(160deg, var(--brand-blue) 0%, var(--brand-blue) 45%, var(--brand-green) 100%);
  }
  .contact-details {
    position: absolute; right: 26px; top: 88px;
    text-align: right; color: var(--card-white);
    font-family: "Source Sans 3", sans-serif;
  }
  .holder-name { font-size: 18px; font-weight: 400; line-height: 21px; letter-spacing: 0.1px; }
  .holder-role { font-size: 12.5px; line-height: 15px; }
  .holder-quals { font-size: 12.5px; font-style: italic; line-height: 15.8px; }
  .contact-list { list-style: none; margin-top: 20px; font-size: 12.5px; line-height: 16px; }
  .contact-list li { display: flex; justify-content: flex-end; align-items: center; gap: 3px; }
  .contact-list svg { width: 10px; height: 10px; fill: var(--card-white); }

  /* Brand side */
  .card--brand { left: 624px; background: var(--card-white); }
  .ghost-area {
    position: absolute; left: -2px; top: 0; width: 228px; height: 265px;
    border-radius: 114px 114px 12px 12px;
    background: linear-gradient(180deg, rgba(255,255,255,0) 0%, var(--ghost-grey) 100%);
    opacity: 0.8;
  }
  .brand-lockup {
    position: absolute; left: 97px; top: 104px;
    display: flex; align-items: center; gap: 18px;
  }
  .brand-dot {
    width: 40px; height: 40px; border-radius: 50%;
    background: var(--brand-blue);
  }
  .brand-name {
    font-family: "Raleway", sans-serif; font-weight: 400;
    font-size: 26px; color: var(--ink-dark); letter-spacing: 0.2px;
  }
  .tagline {
    position: absolute; left: 0; right: 0; top: 221px;
    text-align: center;
    font-family: "Source Sans 3", sans-serif; font-weight: 600;
    font-size: 11.5px; letter-spacing: -0.2px; color: var(--ink-tagline);
    text-transform: uppercase;
  }
</style>
</head>
<body>
<main class="canvas">

  <section class="card card--contact" aria-label="Business card, contact side">
    <div class="contact-panel"></div>
    <div class="symbol-area" role="img" aria-label="Large brand symbol decoration in blue and green"></div>
    <div class="contact-details">
      <p class="holder-name">DARA WHELBY</p>
      <p class="holder-role">Counsellor &amp; Psychotherapist</p>
      <p class="holder-quals">MA (Clin. Psych.), BSc</p>
      <p class="holder-quals">Dip. (Family &amp; Syst.),</p>
      <p class="holder-quals">PG.Dip (DBT), FGTrK, ONRE</p>
      <ul class="contact-list">
        <li>087 5520 194
          <svg viewBox="0 0 10 10" aria-hidden="true"><path d="M1 3c0-1 1-2 4-2s4 1 4 2v1H7V3H3v1H1zM2 5h6l1 4H1z"/></svg>
        </li>
        <li>info@brightwelllane.com
          <svg viewBox="0 0 10 10" aria-hidden="true"><path d="M0 2h10v6H0z"/><path d="M1 2.8 5 5.5 9 2.8" fill="none" stroke="#45b3ec" stroke-width="0.8"/></svg>
        </li>
        <li>www.brightwelllane.com
          <svg viewBox="0 0 10 10" aria-hidden="true"><circle cx="5" cy="5" r="4.6"/></svg>
        </li>
      </ul>
    </div>
  </section>

  <section class="card card--brand" aria-label="Business card, brand side">
    <div class="ghost-area" role="img" aria-label="Faint large brand symbol decoration in soft grey"></div>
    <div class="brand-lockup">
      <span class="brand-dot" aria-hidden="true"></span>
      <span class="brand-name">Brightwell Lane</span>
    </div>
    <p class="tagline">Supporting your mental health and growth is what we do best</p>
  </section>

</main>
</body>
</html>
```